The quiet harbor with an elephant incorporated in the background

Target Market(s)

Real estate

Industry/Entity Type

Real Estate

Contact Information for Business Card

On back on want my name & number
In front I want the business name, "the quiet harbor", below to say staging & design

Logo Text

The quiet harbor

Font styles to use
Serif

Colors
000000

Requirements
Must have
• I want an elephant behind the writing in gold transperant

```html
<!DOCTYPE html>
<html lang="en">
<head>
<meta charset="utf-8">
<title>The Quiet Harbor — Business Card</title>
<link rel="stylesheet" href="https://fonts.googleapis.com/css2?family=Lato:wght@400;700&family=Tinos&display=swap">
<style>
  :root {
    --canvas: #e4e4e4;
    --card: #050505;
    --gold: #c9a24a;
    --white: #f4f4f4;
    --muted: #cfcfcf;
  }
  * { box-sizing: border-box; margin: 0; padding: 0; }
  html, body { width: 1200px; height: 1200px; overflow: hidden; }
  body {
    background: var(--canvas);
    position: relative;
    font-family: "Lato", sans-serif;
  }
  .card {
    position: absolute;
    left: 250px;
    width: 700px;
    height: 400px;
    background: var(--card);
    box-shadow: 0 6px 18px rgba(0,0,0,0.25);
    overflow: hidden;
  }
  .card--back { top: 120px; }
  .card--front { top: 640px; }

  .mark {
    position: absolute;
    border: 5px solid var(--gold);
    border-radius: 50%;
    display: flex;
    align-items: center;
    justify-content: center;
    text-align: center;
  }
  .mark__name {
    font-family: "Lato", sans-serif;
    font-weight: 700;
    color: var(--gold);
    text-transform: uppercase;
    line-height: 1.2;
  }
  .card--back .mark {
    left: 265px; top: 115px; width: 170px; height: 170px;
  }
  .card--back .mark__name { font-size: 17px; letter-spacing: 1px; }

  .card--front .mark {
    left: 95px; top: 150px; width: 170px; height: 170px;
  }
  .card--front .mark__name { font-size: 17px; letter-spacing: 1px; }

  .rule {
    position: absolute;
    left: 262px; right: 0;
    top: 205px;
    height: 7px;
    background: var(--gold);
  }
  .business-name {
    position: absolute;
    left: 290px; top: 160px;
    font-family: "Lato", sans-serif;
    font-weight: 700;
    font-size: 30px;
    color: var(--white);
    text-transform: uppercase;
    letter-spacing: 0.5px;
  }
  .tagline {
    position: absolute;
    left: 292px; top: 224px;
    font-family: "Tinos", serif;
    font-size: 17px;
    color: var(--muted);
    text-transform: uppercase;
    letter-spacing: 2px;
  }
  .person {
    position: absolute;
    left: 345px; top: 268px;
    font-family: "Lato", sans-serif;
    font-weight: 700;
    font-size: 33px;
    color: var(--white);
    text-transform: uppercase;
  }
  .phone {
    position: absolute;
    left: 348px; top: 318px;
    font-family: "Tinos", serif;
    font-size: 21px;
    color: var(--white);
    letter-spacing: 1px;
  }
</style>
</head>
<body>
  <section class="card card--back" aria-label="Card back">
    <div class="mark"><span class="mark__name">The Quiet<br>Harbor</span></div>
  </section>

  <section class="card card--front" aria-label="Card front">
    <div class="mark"><span class="mark__name">The Quiet<br>Harbor</span></div>
    <div class="rule"></div>
    <h1 class="business-name">The Quiet Harbor</h1>
    <p class="tagline">Staging &amp; Design</p>
    <p class="person">John Doe</p>
    <p class="phone">T: 123-456-7890</p>
  </section>
</body>
</html>
```